New hardcover book cover

I want a striking, eye-catching cover with title, subtitle and a picture.See for previous book covers: www.brightquillpress.com

Target Market(s)

young, successful entrepreneurs that have built a business in a niche market that they discovered.

Font styles to use
Serif

Colors

Designer to choose colors to be used in the design.

Requirements
Must have
• A book cover that impresses and captures the imagination of those who look at it.
• MY MISTAKE, SORRY.
• Title: Founders Behind the Quiet Trade Boom
• Subtitle: 25 stories of success from
• discovering hidden opportunities
• Author: Dennis Harlow
• Please use the photo attached, thanks.

```html
<!DOCTYPE html>
<html lang="en">
<head>
<meta charset="utf-8">
<title>Founders Behind the Quiet Trade Boom — Book Cover</title>
<link rel="stylesheet" href="https://fonts.googleapis.com/css2?family=Cinzel:wght@400&family=Josefin+Sans:wght@300&display=swap">
<style>
  :root {
    --stage: #1c1c1c;
    --cover-dark: #3a3a3a;
    --ivory: #f4f2ee;
    --muted: #cfcac2;
    --gold: #d9a66e;
    --accent-red: #e2231a;
    --photo-light: #dcdcda;
    --photo-mid: #9a9a98;
    --wood: #c98a4e;
  }
  * { margin: 0; padding: 0; box-sizing: border-box; }
  html, body {
    width: 1200px;
    height: 905px;
    overflow: hidden;
    background: var(--stage);
  }
  .book-cover {
    position: absolute;
    left: 330px;
    top: 20px;
    width: 540px;
    height: 865px;
    background: var(--cover-dark);
    overflow: hidden;
  }
  .cover-photo {
    position: absolute;
    left: 0;
    top: 0;
    width: 540px;
    height: 424px;
    background: linear-gradient(100deg, var(--photo-light) 0%, var(--photo-mid) 55%, var(--photo-light) 82%, var(--wood) 100%);
  }
  .accent-bar {
    position: absolute;
    right: 0;
    top: 419px;
    width: 195px;
    height: 5px;
    background: var(--accent-red);
  }
  .title-block {
    position: absolute;
    left: 0;
    top: 478px;
    width: 540px;
    text-align: center;
    font-family: "Cinzel", serif;
    font-weight: 400;
    line-height: 1;
  }
  .title-lead {
    color: var(--ivory);
    font-size: 40px;
    letter-spacing: 1px;
  }
  .title-row {
    display: flex;
    justify-content: center;
    align-items: flex-end;
    gap: 8px;
    margin-top: 2px;
  }
  .title-small {
    color: var(--ivory);
    font-size: 25px;
    line-height: 0.9;
    text-align: right;
    padding-bottom: 6px;
  }
  .title-key {
    color: var(--ivory);
    font-size: 70px;
  }
  .title-gold {
    color: var(--gold);
    font-size: 66px;
    margin-top: 2px;
  }
  .subtitle {
    position: absolute;
    left: 0;
    top: 752px;
    width: 540px;
    text-align: center;
    color: var(--muted);
    font-family: "Josefin Sans", sans-serif;
    font-weight: 300;
    font-size: 16px;
    letter-spacing: 1px;
    line-height: 1.3;
  }
  .author {
    position: absolute;
    left: 0;
    top: 805px;
    width: 540px;
    text-align: center;
    color: var(--ivory);
    font-family: "Josefin Sans", sans-serif;
    font-weight: 300;
    font-size: 34px;
    letter-spacing: 6px;
    text-transform: uppercase;
  }
</style>
</head>
<body>
  <main class="book-cover">
    <div class="cover-photo" role="img" aria-label="Photo of a dartboard with a dart in the bullseye"></div>
    <div class="accent-bar"></div>
    <h1 class="title-block">
      <div class="title-lead">FOUNDERS</div>
      <div class="title-row">
        <span class="title-small">BEHIND<br>THE</span>
        <span class="title-key">QUIET</span>
      </div>
      <div class="title-gold">TRADE</div>
      <div class="title-gold">BOOM</div>
    </h1>
    <p class="subtitle">25 stories of success from<br>discovering hidden opportunities</p>
    <p class="author">Dennis Harlow</p>
  </main>
</body>
</html>
```